TalkHarbor - Language Coaching Services

Sleek, innovative, trendy design for Language Coaching business.

TalkHarbor is a new UK based company that provides Language Coaching services. We offer highly personalized on-line and face to face language courses. We also impart learning techniques workshops based on the latest neuroscience research for second-language acquisition.

Target Market(s)

See attached info

Industry/Entity Type

Consulting

Contact Information for Business Card

TalkHarbor
DaniaKV@talkharbor.co.uk
TalkHarbor.co.uk
London, UK

Font styles to use
Sans Serif

```html
<!DOCTYPE html>
<html lang="en">
<head>
<meta charset="utf-8">
<title>TalkHarbor Business Card</title>
<link href="https://fonts.googleapis.com/css2?family=Lato:wght@400;700&display=swap" rel="stylesheet">
<style>
  :root {
    --backdrop: #35302d;
    --card: #111111;
    --card-edge: #1c1c1c;
    --brand-blue: #1b9ad6;
    --silver: #d9d9d9;
    --text-light: #e6e6e6;
    --divider: #3a3a3a;
  }
  * { margin: 0; padding: 0; box-sizing: border-box; }
  html, body {
    width: 1200px; height: 844px; overflow: hidden;
    background: var(--backdrop);
    font-family: "Lato", sans-serif;
  }
  .stage {
    width: 1200px; height: 844px;
    display: flex; align-items: center; justify-content: center; gap: 60px;
  }
  .card {
    width: 520px; height: 298px;
    background: var(--card);
    border: 1px solid var(--card-edge);
    box-shadow: 0 10px 30px rgba(0,0,0,.45);
    position: relative;
  }
  /* contact side */
  .card--contact { display: flex; align-items: center; }
  .brand-block {
    width: 250px; display: flex; flex-direction: column; align-items: center; gap: 18px;
  }
  .brand-mark {
    width: 92px; height: 92px; border-radius: 50%;
    border: 7px solid var(--brand-blue);
  }
  .brand-name {
    font-weight: 700; font-size: 30px; letter-spacing: 1px;
    color: var(--brand-blue); text-transform: uppercase;
  }
  .divider {
    width: 1px; height: 160px; background: var(--divider);
  }
  .details { padding-left: 24px; color: var(--text-light); }
  .person-name {
    font-weight: 700; font-size: 19px; letter-spacing: .5px;
    color: var(--brand-blue); text-transform: uppercase; line-height: 1.1;
  }
  .person-role { font-size: 14px; margin-bottom: 14px; }
  .location { font-size: 14px; margin-bottom: 14px; }
  .contact-list { list-style: none; font-size: 14px; line-height: 1.55; }
  .contact-list li { display: flex; align-items: center; gap: 8px; }
  .contact-list svg { width: 12px; height: 12px; flex: none; }
  /* brand side */
  .card--brand {
    display: flex; flex-direction: column; align-items: center; justify-content: center; gap: 24px;
  }
  .card--brand .brand-mark {
    width: 96px; height: 96px; border-color: var(--silver); border-width: 6px;
  }
  .card--brand .brand-name { color: var(--silver); font-size: 36px; letter-spacing: 2px; }
</style>
</head>
<body>
<main class="stage">
  <section class="card card--contact">
    <div class="brand-block">
      <div class="brand-mark"></div>
      <div class="brand-name">TalkHarbor</div>
    </div>
    <div class="divider"></div>
    <div class="details">
      <h1 class="person-name">Marcus Hale</h1>
      <p class="person-role">Managing Director</p>
      <p class="location">London, UK</p>
      <ul class="contact-list">
        <li>
          <svg viewBox="0 0 12 12"><rect x="2.5" y="0.5" width="7" height="11" rx="1.2" fill="none" stroke="#1b9ad6" stroke-width="1.2"/><circle cx="6" cy="9.5" r=".8" fill="#1b9ad6"/></svg>
          044 555 0142
        </li>
        <li>
          <svg viewBox="0 0 12 12"><rect x="0.5" y="2" width="11" height="8" fill="#1b9ad6"/><path d="M0.5 2 L6 6.5 L11.5 2" fill="none" stroke="#111" stroke-width="1"/></svg>
          DaniaKV@talkharbor.co.uk
        </li>
        <li>
          <svg viewBox="0 0 12 12"><circle cx="6" cy="6" r="5.5" fill="#1b9ad6"/><path d="M0.5 6 H11.5 M6 0.5 C3 3.5 3 8.5 6 11.5 M6 0.5 C9 3.5 9 8.5 6 11.5" fill="none" stroke="#111" stroke-width=".8"/></svg>
          www.TalkHarbor.co.uk
        </li>
      </ul>
    </div>
  </section>

  <section class="card card--brand">
    <div class="brand-mark"></div>
    <div class="brand-name">TalkHarbor</div>
  </section>
</main>
</body>
</html>
```